Tech business card design

We need an amazing business card design for our new business 'Pexla' a marketing tech startup based in Sydney, Australia. We provide an online marketplace for businesses to search and buy advertising media, connect with service providers and learn more about marketing. We wish to communicate 'cool tech', reliability and professionalism and design based around our logo.

Target Market(s)

Business Owners

Contact Information for Business Card

Name
Position
Email Address
Website
Phone Number

Font styles to use
Other font styles liked:
• Avenir & Avenir Next

Colors

Designer to choose colors to be used in the design.

```html
<!DOCTYPE html>
<html lang="en">
<head>
<meta charset="utf-8">
<title>Pexla Business Card</title>
<link href="https://fonts.googleapis.com/css2?family=Roboto:wght@400;500;900&display=swap" rel="stylesheet">
<style>
  :root {
    --navy: #13153b;
    --navy-soft: #1d2050;
    --white: #ffffff;
    --muted: #c9cbe0;
    --backdrop: #b9b9bb;
  }
  * { margin: 0; padding: 0; box-sizing: border-box; }
  html, body {
    width: 1200px; height: 930px; overflow: hidden;
    background: var(--backdrop);
    font-family: "Roboto", Arial, sans-serif;
  }
  .stage { position: relative; width: 1200px; height: 930px; }
  .card {
    position: absolute; width: 520px; height: 300px;
    border-radius: 22px; overflow: hidden;
    background: var(--navy);
    box-shadow: 0 6px 14px rgba(0,0,0,0.25);
  }
  .card--front { left: 90px; top: 120px; }
  .card--back { left: 590px; top: 500px; }

  .wordmark {
    font-weight: 900; color: var(--white);
    letter-spacing: -1px; line-height: 1;
  }
  .card--front .wordmark-wrap {
    position: absolute; inset: 0;
    display: flex; align-items: center; justify-content: center;
  }
  .card--front .wordmark { font-size: 86px; }
  .tm {
    font-size: 10px; font-weight: 500; color: var(--white);
    align-self: flex-end; margin: 0 0 12px 6px;
  }

  .back-art { position: absolute; inset: 0; }
  .card--back .wordmark-wrap {
    position: absolute; left: 290px; top: 62px;
    display: flex; align-items: flex-end;
  }
  .card--back .wordmark { font-size: 62px; color: var(--navy); }
  .card--back .tm { color: var(--navy); margin-bottom: 8px; }

  .contact {
    position: absolute; left: 36px; top: 140px; color: var(--white);
  }
  .contact__name { font-size: 20px; font-weight: 500; }
  .contact__role { font-size: 12px; color: var(--muted); margin: 2px 0 12px 0; }
  .contact__address { font-size: 13px; line-height: 1.35; margin-bottom: 12px; }
  .contact__list { list-style: none; font-size: 13px; line-height: 1.5; }
  .contact__list li { display: flex; align-items: center; gap: 9px; }
  .contact__list svg { width: 10px; height: 10px; flex: none; }
</style>
</head>
<body>
<main class="stage">
  <section class="card card--front" aria-label="Card front">
    <div class="wordmark-wrap">
      <span class="wordmark">pexla</span><span class="tm">TM</span>
    </div>
  </section>

  <section class="card card--back" aria-label="Card back">
    <svg class="back-art" viewBox="0 0 520 300" aria-hidden="true">
      <defs>
        <linearGradient id="sheen" x1="0" x2="1" y1="0" y2="0">
          <stop offset="0" stop-color="#13153b"/>
          <stop offset="0.55" stop-color="#13153b"/>
          <stop offset="0.75" stop-color="#2a2d5e"/>
          <stop offset="1" stop-color="#1a1c47"/>
        </linearGradient>
      </defs>
      <rect width="520" height="300" fill="url(#sheen)"/>
      <circle cx="388" cy="112" r="182" fill="none" stroke="#ffffff" stroke-width="3"/>
      <circle cx="400" cy="100" r="178" fill="#ffffff"/>
    </svg>

    <div class="wordmark-wrap">
      <span class="wordmark">pexla</span><span class="tm">TM</span>
    </div>

    <div class="contact">
      <p class="contact__name">Daniel Reyes</p>
      <p class="contact__role">Director</p>
      <p class="contact__address">2910 Cedar Lane<br>Raleigh, NC 27605</p>
      <ul class="contact__list">
        <li>
          <svg viewBox="0 0 10 10"><path d="M2 1l2 2-1 1.2c.6 1.2 1.5 2.1 2.8 2.8L7 6l2 2-1.3 1.3C4.5 9 1 5.5.7 2.3z" fill="#fff"/></svg>
          +330 5182-7394
        </li>
        <li>
          <svg viewBox="0 0 10 10"><rect x="0.6" y="2" width="8.8" height="6" fill="none" stroke="#fff" stroke-width="1"/><path d="M.6 2l4.4 3.2L9.4 2" fill="none" stroke="#fff" stroke-width="1"/></svg>
          info@pexla.com
        </li>
        <li>
          <svg viewBox="0 0 10 10"><circle cx="5" cy="5" r="4.3" fill="none" stroke="#fff" stroke-width="1"/><path d="M.7 5h8.6M5 .7c-2 2.4-2 6.2 0 8.6M5 .7c2 2.4 2 6.2 0 8.6" fill="none" stroke="#fff" stroke-width="0.8"/></svg>
          www.pexla.com
        </li>
      </ul>
    </div>
  </section>
</main>
</body>
</html>
```